Flyer für Vermietung und Verkauf von Hüpfburgen, aufblasbaren Festzelten und aufblasbaren Hindernisparcours
Flyer für Vermietung und Verkauf von Hüpfburgen, aufblasbaren Festzelten und aufblasbaren Hinder..
Zielgruppe
Wir vermieten und verkaufen Hüpfburgen, aufblasbare Festzelte und aufblasbare Hindernisparcours. Ebenso Sport- und Fungeräte mit Augmented Reality. Für den aktuelen Flyer sollen Vereine, Städte, Gemeinden und Private für den Fasching angesprochen werden.
Aufgabenstellung
Der Flyer soll A4 sein mit 6 Bildern.
Als Text soll enthalten sein:
Slogan: Ihre Faschingsparty mit unseren aufblasbaren Highlights (bessere Ideen sind gerne gefragt)
Text: Machen Sie mit unseren aufblasbaren Hinguckern Ihre Faschingsparty zum absoluten Highlight.
Ganz gleich, ob in der Firma oder privat, für jeden Anlass bieten wir die passende Ergänzung.
Spiele, Hüpfburgen, Sport-Parcours oder Festzelte mit Beleuchtung, wir bieten Ihnen unbegrenzte Möglichkeiten für Ihre Party.
Kontakt:
Bei Interesse kontaktieren Sie uns bitte via Email!
Sabine Krämpel sa.kraempel@blasowind.biz
Seebrunn (Germany) - Altwald (Austria)

```html
<!DOCTYPE html>
<html lang="de">
<head>
<meta charset="utf-8">
<title>Blasowind – Fasching Flyer</title>
<link href="https://fonts.googleapis.com/css2?family=Bebas+Neue&family=Poppins:wght@400;500;600;700&display=swap" rel="stylesheet">
<style>
  :root {
    --hero-red: #d9554f;
    --hero-red-deep: #c6433f;
    --paper: #f2f1f1;
    --white: #ffffff;
    --ink: #1d1d1d;
    --accent: #e63a2e;
    --duck-yellow: #f7d31a;
    --duck-shade: #e3a90d;
  }
  * { margin: 0; padding: 0; box-sizing: border-box; }
  html, body { width: 849px; height: 1200px; overflow: hidden; background: var(--paper); }
  .flyer {
    position: relative; width: 849px; height: 1200px; overflow: hidden;
    background: var(--paper);
    font-family: "Poppins", sans-serif;
  }
  .hero-photo {
    position: absolute; inset: 0;
    background: linear-gradient(180deg, var(--hero-red-deep) 0%, var(--hero-red) 45%, #dc6a5d 100%);
    clip-path: polygon(0 0, 100% 0, 100% 668px, 0 903px);
  }
  .brand-box {
    position: absolute; left: 57px; top: 0; width: 161px; height: 160px;
    background: var(--white);
    display: flex; flex-direction: column; align-items: center; justify-content: center;
  }
  .brand-row { display: flex; align-items: center; gap: 6px; }
  .brand-dot { width: 14px; height: 14px; border-radius: 50%; background: var(--accent); }
  .brand-name { font-weight: 600; font-size: 21px; color: #3b3b3b; letter-spacing: 0.2px; }
  .brand-tagline { font-size: 8px; color: #555; margin-top: 2px; margin-left: 34px; line-height: 1.2; }
  .headline {
    position: absolute; left: 57px; top: 228px;
    font-family: "Bebas Neue", sans-serif; font-weight: 400;
    font-size: 55px; line-height: 61px; color: var(--white); letter-spacing: 0.5px;
  }
  .intro {
    position: absolute; left: 57px; top: 510px; width: 470px;
    font-size: 18.6px; line-height: 30.8px; color: var(--white);
  }
  .product-circle {
    position: absolute; width: 196px; height: 196px; border-radius: 50%;
    background: var(--white); border: 4px solid #f4f1f0;
    display: flex; align-items: center; justify-content: center;
  }
  .product-circle .visual { width: 150px; height: 110px; border-radius: 14px; }
  .c1 { left: 572px; top: 294px; }
  .c2 { left: 572px; top: 493px; }
  .c3 { left: 572px; top: 679px; }
  .v-croc { background: linear-gradient(135deg, #4fae3a, #f1d02a 55%, #2f7fc4); }
  .v-slide { background: linear-gradient(180deg, #f1d02a, #d23a2a 55%, #4fae3a); width: 110px !important; height: 150px !important; }
  .v-tiki { background: linear-gradient(180deg, #3a8a3a 0%, #3a8a3a 35%, #c98a4a 36%, #e3c79a 100%); }
  .duck {
    position: absolute; left: -20px; top: 800px; width: 340px; height: 420px;
    border-radius: 48% 52% 30% 30% / 40% 40% 20% 20%;
    background: radial-gradient(circle at 45% 30%, var(--duck-yellow) 0%, var(--duck-yellow) 55%, var(--duck-shade) 100%);
  }
  .contact {
    position: absolute; right: 57px; top: 950px; text-align: right;
    font-size: 18.4px; line-height: 29px; font-weight: 500; color: var(--ink);
  }
  .social { position: absolute; right: 57px; top: 1078px; display: flex; gap: 12px; }
  .social span { width: 31px; height: 31px; border-radius: 50%; background: var(--accent); }
  .company {
    position: absolute; right: 57px; top: 1122px;
    font-size: 18.6px; font-weight: 700; color: var(--ink);
  }
</style>
</head>
<body>
<main class="flyer">
  <div class="hero-photo" role="img" aria-label="Fotografie eines aufblasbaren Wasserparks auf einem See mit roter Farbüberlagerung"></div>

  <div class="brand-box">
    <div class="brand-row"><span class="brand-dot"></span><span class="brand-name">blasowind</span></div>
    <div class="brand-tagline">Mehr Luft –<br>mehr Spaß</div>
  </div>

  <h1 class="headline">Feiern Sie Fasching<br>im Stil mit unseren<br>aufblasbaren<br>Highlights</h1>

  <p class="intro">Machen Sie mit unseren aufblasbaren Hingu-<br>ckern Ihre Faschingsparty zum absoluten<br>Highlight. Ganz gleich, ob in der Firma oder<br>privat, für jeden Anlass bieten wir die pas-<br>sende Ergänzung. Spiele, Hüpfburgen,<br>Sport-Parcours oder Festzelte mit Beleuch-<br>tung, wir bieten Ihnen unbegrenzte Möglich-<br>keiten für Ihre Party.</p>

  <div class="product-circle c1"><div class="visual v-croc" role="img" aria-label="Hüpfburg in Krokodilform"></div></div>
  <div class="product-circle c2"><div class="visual v-slide" role="img" aria-label="Aufblasbare Rutsche"></div></div>
  <div class="product-circle c3"><div class="visual v-tiki" role="img" aria-label="Aufblasbare Tiki-Bar"></div></div>

  <div class="duck" role="img" aria-label="Große aufblasbare gelbe Badeente"></div>

  <div class="contact">
    Bei Interesse kontaktieren Sie uns bitte via Email!<br>
    Sabine Krämpel sa.kraempel@blasowind.biz<br>
    Seebrunn (Germany) - Altwald (Austria)
  </div>

  <div class="social" aria-label="Soziale Netzwerke"><span></span><span></span><span></span><span></span></div>

  <div class="company">Blasowind GmbH</div>
</main>
</body>
</html>
```